Naturopath Practitioner Card Design

I am a naturopath needing a design for a business card mainly to show that I am a naturopath and have some contact details to give to prospective clients. I am open minded about the design and what is on the second side of the card whether it just be some artwork or space for details, appointment times etc. Naturopathy is the practice of natural medicine that uses a holistic approach and incorporates herbal and nutritional medicine.

Industry/Entity Type

Business

Contact Information for Business Card

Tom Rudd NaturopathBHSc (Naturopathy) Member WHPG 0487 925 316 tom.rudd@mailexample.com www.tomruddnaturopathy.example.au

Requirements
Nice to have
• Would prefer some kind of original pattern/art work/logo rather than an image, not fussed if its very simple/basic
• I am open to any colour but think I would prefer a more earthy sandy clay etc type style than the greens that are commonly associated with naturopathy.
Should not have
• Don't really want to have generic stock images on it

```html
<!DOCTYPE html>
<html lang="en">
<head>
<meta charset="utf-8">
<title>Tom Rudd Naturopath – Business Card</title>
<link rel="stylesheet" href="https://fonts.googleapis.com/css2?family=Arimo:wght@400&family=Questrial&display=swap">
<style>
  :root {
    --backdrop: #a8a8a8;
    --card-light: #ffffff;
    --card-earth: #6e5e3b;
    --olive: #6f6034;
    --sand-gold: #cdb978;
    --text-grey: #6b6b6b;
    --text-dark: #2b2b2b;
    --url-light: #ece6d4;
  }
  * { margin: 0; padding: 0; box-sizing: border-box; }
  html, body { width: 1200px; height: 600px; overflow: hidden; }
  body {
    background: var(--backdrop);
    position: relative;
    font-family: "Arimo", Arial, sans-serif;
  }
  .card {
    position: absolute;
    top: 162px;
    width: 500px;
    height: 276px;
    border-radius: 0 120px 0 120px;
    text-align: center;
  }
  .card--front { left: 60px; background: var(--card-light); }
  .card--back { left: 640px; background: var(--card-earth); }

  .brand-mark {
    display: flex;
    align-items: center;
    justify-content: center;
    gap: 8px;
    font-family: "Questrial", Arial, sans-serif;
    font-weight: 400;
  }
  .brand-mark__dot { width: 12px; height: 12px; border-radius: 50%; }

  .card--front .brand-mark { position: absolute; top: 82px; left: 0; right: 0; color: var(--olive); font-size: 20px; }
  .card--front .brand-mark__dot { background: var(--olive); }

  .front__name { position: absolute; top: 172px; left: 0; right: 0; font-size: 19px; color: var(--text-grey); }
  .front__credentials { position: absolute; top: 200px; left: 0; right: 0; font-size: 10.5px; color: var(--olive); }
  .front__contacts {
    position: absolute; top: 228px; left: 0; right: 0;
    display: flex; justify-content: center; gap: 18px;
    font-size: 13px; color: var(--text-dark);
  }
  .contact { display: flex; align-items: center; gap: 5px; }
  .contact svg { fill: var(--olive); }

  .card--back .brand-mark { position: absolute; top: 78px; left: 0; right: 0; color: var(--sand-gold); font-size: 20px; }
  .card--back .brand-mark__dot { background: var(--sand-gold); }
  .back__name {
    position: absolute; top: 140px; left: 0; right: 0;
    font-family: "Questrial", Arial, sans-serif;
    font-size: 34px; letter-spacing: 2px; color: var(--sand-gold);
  }
  .back__role {
    position: absolute; top: 184px; left: 0; right: 0;
    font-family: "Questrial", Arial, sans-serif;
    font-size: 11px; letter-spacing: 5px; color: var(--sand-gold);
  }
  .back__web {
    position: absolute; top: 226px; left: 0; right: 0;
    font-size: 13px; letter-spacing: 0.8px; color: var(--url-light);
  }
</style>
</head>
<body>
  <section class="card card--front" aria-label="Card front">
    <div class="brand-mark"><span class="brand-mark__dot"></span><span>Tom Rudd</span></div>
    <p class="front__name">Tom Rudd</p>
    <p class="front__credentials">NaturopathBHSc (Naturopathy) Member WHPG</p>
    <div class="front__contacts">
      <span class="contact">
        <svg width="15" height="11" viewBox="0 0 15 11" aria-hidden="true"><path d="M1 3.5C1 1.5 4 0.5 7.5 0.5S14 1.5 14 3.5V4.5H10.5V3H4.5V4.5H1Z"/><path d="M3 5.5H12L13 10.5H2Z"/></svg>
        0487 925 316
      </span>
      <span class="contact">
        <svg width="15" height="10" viewBox="0 0 15 10" aria-hidden="true"><path d="M0 0H15V10H0Z"/><path d="M0 0L7.5 5.5L15 0" fill="none" stroke="#fff" stroke-width="1"/></svg>
        tom.rudd@mailexample.com
      </span>
    </div>
  </section>

  <section class="card card--back" aria-label="Card back">
    <div class="brand-mark"><span class="brand-mark__dot"></span><span>Tom Rudd</span></div>
    <p class="back__name">Tom Rudd</p>
    <p class="back__role">Naturopath</p>
    <p class="back__web">www.tomruddnaturopathy.example.au</p>
  </section>
</body>
</html>
```